Skin Care Logo and Package Design

We need a Logo and Label design for our new skin care line we are launching in our medical spa here in Atlanta. Our medical spa provides high end skin care and body contouring treatments like Vexaforming, laser treatments, facials and chemical peels. I would like to see a clean, sleek, modern feel. i am attaching a picture of the packaging we will being using. Please keep in mind the Serum and Cream jar containers will be packaged in a white box. This packaging is the Morvie packaging in attached document.) The tall bottles (Seraphine Collection) will be for facial cleansers and body lotions, these will not have a box. Please refer to attached file. Thank you.

Target Market(s)

Anti-Aging men and women age 30 to 65

Requirements
Must have
• Logo: the name of the product: Davoria Clinical
Design and lay out for Bottle: See attached download of packaging, Face cleanser bottle is the "Seraphine" Collection, this bottle will be used for all cleansers, toners, and body lotions.
Design and lay out for Serum and Face cream package: This will be the "Morvie" Collection, see attached pdf for picture. Both products will have white boxes so we will need a designed label for box.

Also, I have included our company logo to our med spa. I wouldn't mind something that follows close to our brand.
Nice to have
• Like to have a modern, sophisticated, yet simple. Maybe add a nature flair to the design?
Should not have
• Lots of Color

```html
<!DOCTYPE html>
<html lang="en">
<head>
<meta charset="utf-8">
<title>Davoria Clinical – Skin Care Labels</title>
<link rel="stylesheet" href="https://fonts.googleapis.com/css2?family=Open+Sans:wght@400;600&display=swap">
<style>
  :root {
    --ink: #2b2b2b;
    --ink-soft: #444444;
    --olive: #a09d4c;
    --leaf: #e3f0dc;
    --leaf-deep: #cfe5c4;
    --panel: #ffffff;
    --bg-top: #ffffff;
    --bg-bottom: #e9eeec;
    --black-band: #151515;
  }
  * { box-sizing: border-box; margin: 0; padding: 0; }
  html, body { width: 1200px; height: 1200px; overflow: hidden; }
  body {
    font-family: "Open Sans", sans-serif;
    color: var(--ink);
    background: linear-gradient(180deg, var(--bg-top) 0%, var(--bg-top) 30%, var(--bg-bottom) 100%);
    position: relative;
  }
  .label {
    position: absolute;
    background: var(--panel);
    box-shadow: 0 6px 24px rgba(0,0,0,0.07);
    text-align: center;
    overflow: hidden;
  }
  .leaf-area {
    position: absolute;
    left: 0; right: 0; bottom: 0;
    background: linear-gradient(160deg, rgba(255,255,255,0) 0%, var(--leaf) 55%, var(--leaf-deep) 100%);
    opacity: 0.7;
  }
  .brand {
    position: relative;
    display: flex;
    align-items: center;
    justify-content: center;
    gap: 8px;
    font-weight: 400;
    letter-spacing: 0.22em;
    color: var(--ink);
  }
  .brand-dot {
    border: 1.5px solid var(--ink);
    border-radius: 50%;
  }
  .content { position: relative; }
  .collection-pill {
    display: inline-block;
    background: var(--olive);
    color: #ffffff;
    font-weight: 600;
    letter-spacing: 0.14em;
    border-radius: 8px;
  }
  .divider {
    width: 82px; height: 1px;
    background: var(--olive);
    opacity: 0.6;
    margin: 14px auto;
  }

  /* Serum box front */
  .serum { left: 175px; top: 290px; width: 225px; height: 670px; }
  .serum .brand { margin-top: 90px; font-size: 15px; }
  .serum .brand-dot { width: 14px; height: 14px; }
  .serum .leaf-area { height: 330px; }
  .serum .product-name { margin-top: 110px; font-size: 22px; line-height: 32px; letter-spacing: 0.03em; color: var(--ink-soft); }
  .serum .tagline { font-size: 13.5px; line-height: 19px; color: var(--ink-soft); }
  .serum .collection-pill { margin-top: 178px; width: 188px; font-size: 13px; padding: 1px 0; }
  .serum .volume { margin-top: 40px; font-size: 14px; letter-spacing: 0.04em; }

  /* Cream box front */
  .cream { left: 484px; top: 660px; width: 342px; height: 288px; }
  .cream .brand { margin-top: 90px; font-size: 15px; }
  .cream .brand-dot { width: 14px; height: 14px; }
  .cream .leaf-area { height: 170px; }
  .cream .eyebrow { margin-top: 34px; font-size: 10.5px; color: var(--ink-soft); }
  .cream .product-name { margin-top: 4px; font-size: 10.5px; font-weight: 600; letter-spacing: 0.08em; }
  .cream .collection-pill { margin-top: 38px; width: 194px; font-size: 13px; padding: 1px 0; }
  .cream .volume { margin-top: 18px; font-size: 9.5px; }

  /* Cleanser bottle label */
  .cleanser { left: 870px; top: 470px; width: 176px; height: 500px; border-radius: 70px 70px 16px 16px; }
  .cleanser .brand { margin-top: 168px; font-size: 11px; letter-spacing: 0.16em; gap: 6px; }
  .cleanser .brand-dot { width: 10px; height: 10px; }
  .cleanser .leaf-area { height: 180px; }
  .cleanser .product-name { margin-top: 90px; font-size: 12.5px; line-height: 20px; color: var(--ink-soft); letter-spacing: 0.02em; }
  .cleanser .collection-pill { margin-top: 124px; width: 104px; background: var(--black-band); font-size: 7.5px; letter-spacing: 0.02em; padding: 3px 0; border-radius: 4px; }
  .cleanser .volume { margin-top: 14px; font-size: 9px; }
</style>
</head>
<body>

  <section class="label serum" aria-label="Anti-aging face serum box label">
    <div class="leaf-area" role="img" aria-label="Faint green leaf vein texture"></div>
    <div class="brand"><span class="brand-dot"></span>DAVORIA CLINICAL</div>
    <div class="content">
      <h2 class="product-name">ANTI-AGING<br>FACE SERUM</h2>
      <div class="divider"></div>
      <p class="tagline">high end skin care<br>and body contouring<br>treatments</p>
      <span class="collection-pill">Morvie Collection</span>
      <p class="volume">1floz / 30ml</p>
    </div>
  </section>

  <section class="label cream" aria-label="Anti-aging face cream box label">
    <div class="leaf-area" role="img" aria-label="Faint green leaf vein texture"></div>
    <div class="brand"><span class="brand-dot"></span>DAVORIA CLINICAL</div>
    <div class="content">
      <p class="eyebrow">HIGH END SKIN CARE</p>
      <h2 class="product-name">ANTI-AGING FACE CREAM</h2>
      <span class="collection-pill">Morvie Collection</span>
      <p class="volume">1 floz / 30ml</p>
    </div>
  </section>

  <section class="label cleanser" aria-label="Anti-aging face cleanser bottle label">
    <div class="leaf-area" role="img" aria-label="Faint green leaf vein texture"></div>
    <div class="brand"><span class="brand-dot"></span>DAVORIA CLINICAL</div>
    <div class="content">
      <h2 class="product-name">ANTI-AGING<br>FACE CLEANSER</h2>
      <span class="collection-pill">Seraphine Collection</span>
      <p class="volume">7floz / 200ml</p>
    </div>
  </section>

</body>
</html>
```